Road Construction Company needs business cards

We would like a new business card designed for our business.

We're a road construction company based in Qld, Australia.

Can the business card please have the following information on it.

Name: Warren Halbeck
Position: General Manager
Phone: 0472 915 348
Email: Warren.halbeck@tovrin.com.au
Address: 87 Marrow Ave, Pendlebay, QLD, 4023
Website: www.tovrin.com.au

Visually we'd like the card to be professional and simple.

Attached is our logo.

Our website is www.tovrin.com.au

Target Market(s)

Men aged 25-60

Contact Information for Business Card

As listed in project description

Font styles to use
Serif

Requirements
Must have
• Large logo on back of card

```html
<!DOCTYPE html>
<html lang="en">
<head>
<meta charset="UTF-8">
<title>Tovrin Road Construction – Business Card</title>
<link rel="stylesheet" href="https://fonts.googleapis.com/css2?family=Poppins:wght@300;400;600;700;800&display=swap">
<style>
  :root {
    --backdrop: #3f3f3f;
    --paper: #fbfbfb;
    --brand-navy: #1b4f9e;
    --brand-sky: #3ba3dc;
    --ink-grey: #555a60;
    --night-deep: #0d1e3c;
    --night-blue: #0b4b94;
  }
  * { margin: 0; padding: 0; box-sizing: border-box; }
  html, body {
    width: 1200px; height: 801px; overflow: hidden;
    background: var(--backdrop);
    font-family: "Poppins", sans-serif;
  }
  .stage { position: relative; width: 1200px; height: 801px; }

  .card {
    position: absolute;
    width: 540px; height: 310px;
    border-radius: 3px;
    overflow: hidden;
    box-shadow: 0 18px 40px rgba(0,0,0,0.45);
  }

  /* Front */
  .card-front { left: 70px; top: 90px; background: var(--paper); }
  .brand-name {
    position: absolute; left: 38px; top: 62px;
    font-weight: 800; font-size: 56px; letter-spacing: 1px;
    color: var(--brand-navy); line-height: 1;
  }
  .person { position: absolute; right: 40px; top: 52px; text-align: right; }
  .person-name { font-weight: 700; font-size: 21px; color: var(--brand-navy); line-height: 1.15; }
  .person-role { font-weight: 300; font-size: 14px; color: var(--brand-sky); }
  .address {
    position: absolute; right: 40px; top: 122px;
    display: flex; gap: 6px; align-items: flex-start;
    font-size: 11px; color: var(--ink-grey); line-height: 1.45;
  }
  .address svg { margin-top: 2px; }
  .divider {
    position: absolute; left: 38px; top: 178px;
    width: 300px; height: 1px; background: var(--brand-sky);
  }
  .contacts { position: absolute; left: 38px; top: 192px; list-style: none; }
  .contacts li {
    display: flex; align-items: center; gap: 8px;
    font-size: 12px; color: var(--ink-grey); line-height: 1.6;
  }
  .contacts svg { flex: none; }
  .edge-bands { position: absolute; left: 0; bottom: 0; }

  /* Back */
  .card-back { left: 590px; top: 400px; }
  .back-photo {
    position: absolute; inset: 0;
    background:
      radial-gradient(ellipse at 30% 75%, #0d5bb0 0%, rgba(11,75,148,0) 60%),
      linear-gradient(135deg, var(--night-blue) 0%, #123a72 45%, var(--night-deep) 100%);
  }
  .back-logo {
    position: absolute; left: 0; right: 0; top: 118px;
    text-align: center;
    font-weight: 800; font-size: 64px; letter-spacing: 2px;
    color: #ffffff; line-height: 1;
  }
</style>
</head>
<body>
<main class="stage">

  <section class="card card-front" aria-label="Business card front">
    <div class="brand-name">TOVRIN</div>

    <div class="person">
      <div class="person-name">Warren Halbeck</div>
      <div class="person-role">General Manager</div>
    </div>

    <div class="address">
      <svg width="9" height="12" viewBox="0 0 9 12" aria-hidden="true">
        <path d="M4.5 0C2 0 0 2 0 4.5 0 8 4.5 12 4.5 12S9 8 9 4.5C9 2 7 0 4.5 0zm0 6.3a1.8 1.8 0 1 1 0-3.6 1.8 1.8 0 0 1 0 3.6z" fill="var(--brand-navy)"/>
      </svg>
      <div>87 Marrow Ave,<br>Pendlebay, QLD, 4023</div>
    </div>

    <div class="divider"></div>

    <ul class="contacts">
      <li>
        <svg width="11" height="11" viewBox="0 0 24 24" aria-hidden="true"><path d="M6.6 10.8a15.1 15.1 0 0 0 6.6 6.6l2.2-2.2a1 1 0 0 1 1-.25 11.4 11.4 0 0 0 3.6.57 1 1 0 0 1 1 1V20a1 1 0 0 1-1 1A17 17 0 0 1 3 4a1 1 0 0 1 1-1h3.5a1 1 0 0 1 1 1c0 1.25.2 2.45.57 3.57a1 1 0 0 1-.25 1z" fill="var(--brand-navy)"/></svg>
        0472 915 348
      </li>
      <li>
        <svg width="11" height="11" viewBox="0 0 24 24" aria-hidden="true"><path d="M2 5h20v14H2z" fill="var(--brand-navy)"/><path d="M2 5l10 8 10-8" stroke="#fff" stroke-width="1.8" fill="none"/></svg>
        Warren.halbeck@tovrin.com.au
      </li>
      <li>
        <svg width="11" height="11" viewBox="0 0 24 24" aria-hidden="true"><circle cx="12" cy="12" r="11" fill="var(--brand-navy)"/><path d="M1 12h22M12 1c3.5 3 3.5 19 0 22M12 1c-3.5 3-3.5 19 0 22" stroke="#fff" stroke-width="1.4" fill="none"/></svg>
        www.tovrin.com.au
      </li>
    </ul>

    <svg class="edge-bands" width="540" height="26" viewBox="0 0 540 26" aria-hidden="true">
      <polygon points="0,12 330,12 322,24 0,24" fill="var(--brand-navy)"/>
      <polygon points="340,4 540,4 540,14 334,14" fill="var(--brand-sky)"/>
    </svg>
  </section>

  <section class="card card-back" aria-label="Business card back">
    <div class="back-photo" role="img" aria-label="Dark blue toned photograph of a road roller compacting fresh asphalt"></div>
    <div class="back-logo">TOVRIN</div>
  </section>

</main>
</body>
</html>
```